Redesign of the UI of a customer service platform

To improve the user experience of our customers, we need a new design for our agent interface of our customer service platform (velorant.com).
The focus will be on the dashboard and the inbox screens (see attached) along with the common UI elements (Buttons, menu, fonts, forms...)
We want a simple and distinctive design

Target Market(s)

Worldwide

Industry/Entity Type

It Service

Number of Pages Required

3 page

Font styles to use
Sans Serif

Requirements
Must have
• New Onboarding page: this is a new page that is shown to user the first time they login to the platform. This will replace the current onboarding screen (setup SMS, Setup widget...etc)
• Dashboard page: to access important information and activate services (see screenshot from current site)
• Inbox page: to manage all the interactions with customers. (see screenshot from current site)
• UI elements (buttons, menus, forms, tables, fonts, color palette)

```html
<!DOCTYPE html>
<html lang="en"><head><meta charset="utf-8"><title>velorant — Dashboard</title>
<link href="https://fonts.googleapis.com/css2?family=Roboto:wght@400;500;700&display=swap" rel="stylesheet">
<style>
:root{--orange:#e8522a;--blue:#4a7cf5;--red:#d9262c;--lime:#7cc22a;--green:#22a650;--ink:#333;--side:#e9e9e9;--panel:#f4f4f4;--plan:#ededed;--teal:#1a8fb5;--feedback:#a9e2f5;--dark:#333;--line:#456}
*{box-sizing:border-box;margin:0;padding:0}
html,body{width:776px;height:1200px;overflow:hidden;background:#fff;font-family:Roboto,sans-serif;color:var(--ink)}
.a{position:absolute}
.logo{left:18px;top:38px;font-size:22px;font-weight:700;color:#333;display:flex;align-items:center;gap:4px}
.logo i{width:18px;height:18px;border-radius:50%;background:#333;display:inline-block}
.menu-btn{left:156px;top:40px;width:24px;height:24px;border-radius:50%;background:var(--orange)}
.menu-btn::before{content:"";position:absolute;left:7px;top:8px;width:10px;height:7px;border-top:1px solid #fff;border-bottom:1px solid #fff}
.menu-btn::after{content:"";position:absolute;left:7px;top:11.5px;width:10px;border-top:1px solid #fff}
.top{font-size:10px;color:#333;top:47px}
.badge{width:14px;height:14px;border-radius:50%;background:var(--orange);color:#fff;font-size:8px;text-align:center;line-height:14px}
.avatar{left:627px;top:39px;width:25px;height:25px;border-radius:50%;background:linear-gradient(#c98c6a,#7a4a35)}
.sidebar{left:15px;top:70px;width:131px;height:1112px;background:var(--side)}
.nav{left:15px;width:131px;height:26px;font-size:10px;display:flex;align-items:center;padding-left:37px}
.nav.active{background:var(--orange);color:#fff}
.nav svg{position:absolute;left:13px;top:6px}
.arrow{left:146px;top:80px;border-left:8px solid var(--orange);border-top:13px solid transparent;border-bottom:13px solid transparent}
.feedback{left:15px;top:1136px;width:131px;height:46px;background:var(--feedback);font-size:10px;display:flex;align-items:center;padding-left:37px}
.feedback svg{position:absolute;left:17px;top:18px}
.stats{left:146px;top:70px;width:616px;height:136px;background:var(--panel)}
.h{font-size:13.5px;color:#444}
.tile{width:34px;height:31px;border-radius:2px}
.tile svg{position:absolute;left:8px;top:7px}
.val{font-size:22px;color:#333}
.lbl{font-size:9.5px;color:#333;line-height:11.5px}
.date{left:535px;top:81px;width:176px;height:16px;background:#e6e6e6;font-size:8.5px;line-height:16px;padding-left:20px}
.userbtn{left:724px;top:71px;width:34px;height:32px;background:var(--dark)}
.side-ico{left:729px;width:29px;height:30px}
.plan{left:146px;top:618px;width:616px;height:564px;background:var(--plan)}
.card{top:693px;width:143px;height:126px;background:#fff;text-align:center;font-size:11px;font-weight:500;line-height:14px}
.card .cnt{position:absolute;left:74px;top:10px;width:22px;height:22px;border-radius:50%;background:var(--lime);color:#fff;font-size:7.5px;line-height:22px}
.card svg{position:absolute;left:58px;top:28px}
.card p{position:absolute;top:80px;width:100%}
.addon{left:230px;width:448px;height:67px;background:#fff}
.addon h3{position:absolute;left:12px;top:14px;font-size:10.5px;font-weight:500;color:var(--teal)}
.addon p{position:absolute;left:12px;top:32px;width:330px;font-size:7.2px;line-height:11.5px;color:#333}
.btn{position:absolute;right:13px;top:26px;height:18px;border:1px solid #ccc;border-radius:2px;font-size:7.5px;font-weight:700;line-height:16px;padding:0 10px 0 22px;color:var(--teal);background:#fff}
.btn::before{content:"";position:absolute;left:7px;top:3px;width:9px;height:9px;border:1px solid currentColor;border-radius:50%}
.mark{left:740px;top:1160px;font-size:9px;color:#666}
</style></head><body>
<div class="a logo"><i></i>velorant</div>
<div class="a menu-btn"></div>
<div class="a badge" style="left:426px;top:37px">4</div>
<svg class="a" style="left:432px;top:46px" width="18" height="14" viewBox="0 0 18 14"><path d="M2 5h14v7H2zM2 5l3-4h8l3 4" fill="none" stroke="var(--line)"/></svg>
<div class="a top" style="left:458px">INBOX</div>
<svg class="a" style="left:498px;top:40px" width="24" height="22" viewBox="0 0 24 22"><path d="M3 13 13 3l8 6L11 19z" fill="none" stroke="var(--orange)" stroke-width="1.3"/></svg>
<svg class="a" style="left:534px;top:40px" width="18" height="18" viewBox="0 0 18 18"><circle cx="9" cy="6" r="4" fill="none" stroke="var(--line)"/><path d="M2 17c0-5 14-5 14 0" fill="none" stroke="var(--line)"/></svg>
<div class="a top" style="left:555px">AVAILABLE &nbsp;⌄</div>
<div class="a avatar" role="img" aria-label="Agent profile photo"></div>
<div class="a top" style="left:658px">LENA MORO &nbsp;&nbsp;⌄</div>
<div class="a top" style="left:736px;font-size:13px;font-weight:700;top:44px">?</div>

<div class="a sidebar"></div>
<div class="a nav active" style="top:80px"><svg width="12" height="12" viewBox="0 0 12 12"><path d="M1 6 6 1l5 5v5H1z" fill="none" stroke="#fff"/></svg>Dashboard</div><div class="a arrow"></div>
<div class="a nav" style="top:109px"><svg width="12" height="12" viewBox="0 0 12 12"><path d="M1 5h10v5H1zM1 5l2-3h6l2 3" fill="none" stroke="var(--line)"/></svg>Inbox</div><div class="a badge" style="left:121px;top:115px">4</div>
<div class="a nav" style="top:136px"><svg width="14" height="12" viewBox="0 0 14 12"><path d="M1 7 7 1l6 4-6 6z" fill="none" stroke="var(--line)"/></svg>Tickets</div>
<div class="a nav" style="top:163px"><svg width="14" height="12" viewBox="0 0 14 12"><circle cx="7" cy="4" r="3" fill="none" stroke="var(--line)"/><path d="M1 12c0-4 12-4 12 0" fill="none" stroke="var(--line)"/></svg>Clients</div>
<div class="a nav" style="top:189px"><svg width="12" height="12" viewBox="0 0 12 12"><path d="M1 11h10M2 11V5h2v6M5 11V2h2v9M8 11V6h2v5" fill="none" stroke="var(--line)"/></svg>Reports</div>
<div class="a nav" style="top:217px"><svg width="12" height="12" viewBox="0 0 12 12"><circle cx="6" cy="6" r="4.5" fill="none" stroke="var(--line)" stroke-dasharray="2 1"/><circle cx="6" cy="6" r="1.8" fill="none" stroke="var(--line)"/></svg>Settings<span style="margin-left:44px">‹</span></div>
<div class="a feedback"><svg width="12" height="9" viewBox="0 0 12 9"><path d="M.5.5h11v8H.5zM.5.5 6 5l5.5-4.5" fill="none" stroke="var(--line)"/></svg>Send feedback</div>

<div class="a stats"></div>
<svg class="a" style="left:165px;top:84px" width="22" height="22" viewBox="0 0 22 22"><path d="M2 10 11 2l9 8v10H2z" fill="none" stroke="var(--line)"/><rect x="8" y="13" width="6" height="7" fill="none" stroke="var(--line)"/></svg>
<div class="a h" style="left:197px;top:88px">DASHBOARD</div>
<div class="a date">23 December 2016 - 07 January 2017 ⌄</div>
<div class="a userbtn"><svg style="position:absolute;left:9px;top:8px" width="16" height="16" viewBox="0 0 16 16"><circle cx="8" cy="5" r="3.5" fill="none" stroke="#fff"/><path d="M1 15c0-5 14-5 14 0z" fill="none" stroke="#fff"/></svg></div>
<div class="a tile" style="left:168px;top:130px;background:var(--blue)"><svg width="18" height="17" viewBox="0 0 18 17"><circle cx="9" cy="5" r="4" fill="none" stroke="#fff"/><path d="M1 16c0-6 16-6 16 0z" fill="none" stroke="#fff"/></svg></div><div class="a val" style="left:211px;top:134px">0/0</div><div class="a lbl" style="left:168px;top:171px">Total Clients<br>Served / Non-served</div>
<div class="a tile" style="left:316px;top:130px;background:var(--red)"><svg width="18" height="17" viewBox="0 0 18 17"><path d="M1 10 10 1l7 5-9 10z" fill="none" stroke="#fff"/></svg></div><div class="a val" style="left:359px;top:134px">0/0</div><div class="a lbl" style="left:316px;top:172px">Client Ticket<br>Closed / Opened</div>
<div class="a tile" style="left:451px;top:130px;background:var(--lime)"><svg width="18" height="17" viewBox="0 0 18 17"><ellipse cx="9" cy="8" rx="8" ry="6" fill="none" stroke="#fff"/><circle cx="6" cy="8" r="1" fill="#fff"/><circle cx="9" cy="8" r="1" fill="#fff"/><circle cx="12" cy="8" r="1" fill="#fff"/></svg></div><div class="a val" style="left:494px;top:134px">0</div><div class="a lbl" style="left:452px;top:175px">Total Chat Messages</div>
<div class="a tile" style="left:586px;top:130px;background:var(--green)"><svg width="18" height="17" viewBox="0 0 18 17"><path d="M1 3h16v11H1zM1 3l8 6 8-6" fill="none" stroke="#fff"/></svg></div><div class="a val" style="left:629px;top:134px">0</div><div class="a lbl" style="left:585px;top:174px;color:var(--orange)">Total SMS Messages</div>

<svg class="a" style="left:165px;top:221px" width="26" height="26" viewBox="0 0 26 26"><path d="M1 24h24M4 24V12h4v12M11 24V3h4v21M18 24V9h4v15" fill="none" stroke="var(--line)"/></svg>
<div class="a h" style="left:197px;top:229px">REPORTS</div>
<div class="a" style="left:146px;top:259px;width:616px;text-align:center;font-size:16px;color:#555">Clients total : served vs non-served ( Account )</div>
<div class="a" style="left:146px;top:283px;width:616px;text-align:center;font-size:8px;color:#555">from 23 December 2016 to 97 January 2017</div>
<svg class="a" style="left:181px;top:307px" width="548" height="267" viewBox="181 307 548 267" font-family="Roboto,sans-serif" font-size="9" fill="#fff">
<rect x="181" y="307" width="548" height="267" fill="var(--blue)"/>
<g stroke="#fff" stroke-width=".8"><line x1="231" x2="686" y1="332" y2="332"/><line x1="231" x2="686" y1="365" y2="365"/><line x1="231" x2="686" y1="398" y2="398"/><line x1="231" x2="686" y1="430" y2="430"/><line x1="231" x2="686" y1="462" y2="462"/><line x1="231" x2="686" y1="495" y2="495"/><line x1="231" x2="686" y1="528" y2="528"/>
<path d="M287 528v10M339 528v10M391 528v10M442 528v10M494 528v10M546 528v10M598 528v10M650 528v10"/></g>
<g text-anchor="end"><text x="227" y="335">6</text><text x="227" y="368">5</text><text x="227" y="401">4</text><text x="227" y="433">3</text><text x="227" y="465">2</text><text x="227" y="498">1</text><text x="227" y="528">0</text></g>
<g text-anchor="middle"><text x="287" y="551">24 Dec</text><text x="339" y="551">26 Dec</text><text x="391" y="551">28 Dec</text><text x="442" y="551">30 Dec</text><text x="494" y="551">01 Jan</text><text x="546" y="551">03 Jan</text><text x="598" y="551">05 Jan</text><text x="650" y="551">07 Jan</text></g>
<text x="211" y="404" font-size="14" text-anchor="middle" transform="rotate(-90 211 404)">Clients</text></svg>
<div class="a side-ico" style="top:314px;background:var(--blue)"></div>
<div class="a side-ico" style="top:348px;background:var(--red)"></div>
<div class="a side-ico" style="top:382px;background:var(--lime)"></div>
<div class="a side-ico" style="top:415px;background:var(--green)"></div>
<div class="a" style="left:386px;top:596px;font-size:9.5px"><span style="display:inline-block;width:11px;height:11px;background:#f5741e;vertical-align:-2px"></span> Served &nbsp;&nbsp;<span style="display:inline-block;width:11px;height:11px;background:#444;vertical-align:-2px"></span> Non Served</div>

<div class="a plan"></div>
<svg class="a" style="left:164px;top:626px" width="28" height="28" viewBox="0 0 28 28"><circle cx="14" cy="14" r="13" fill="#fff" stroke="#bbb"/><path d="M14 7v14M7 14h14" stroke="var(--lime)" stroke-width="2.5"/></svg>
<div class="a h" style="left:198px;top:633px">PLAN &amp; ADD ONS</div>
<div class="a" style="left:199px;top:665px;font-size:9.5px">PLAN ( PRO )</div>
<div class="a btn" style="left:266px;right:auto;top:662px;color:var(--green);border-color:#ccc">UPGRADE</div>
<div class="a card" style="left:232px"><span class="cnt">1/1</span><svg width="24" height="22" viewBox="0 0 24 22"><circle cx="12" cy="7" r="5" fill="none" stroke="var(--line)" stroke-width="1.3"/><path d="M2 21c0-7 20-7 20 0z" fill="none" stroke="var(--line)" stroke-width="1.3"/></svg><p>AGENTS<br>UNLIMITED</p></div>
<div class="a card" style="left:383px"><span class="cnt">1</span><svg width="24" height="22" viewBox="0 0 24 22"><rect x="1" y="6" width="22" height="15" rx="2" fill="none" stroke="var(--line)" stroke-width="1.3"/><path d="M8 6V3h8v3M1 12h22" fill="none" stroke="var(--line)" stroke-width="1.3"/></svg><p style="top:77px">DEPARTMENTS<br>UNLIMITED</p></div>
<div class="a card" style="left:534px"><span class="cnt">1</span><svg width="24" height="22" viewBox="0 0 24 22"><rect x="5" y="1" width="13" height="20" rx="2" fill="none" stroke="var(--line)" stroke-width="1.3"/><path d="M10 18h3" stroke="var(--line)"/></svg><p style="top:76px">PHONES<br>UNLIMITED</p></div>
<div class="a addon" style="top:830px"><h3 style="color:var(--orange)">PHONES + SMS</h3><p>Lorem ipsum dolor sit amet, consectetur adipiscing elit, sed do eiusmod tempor incididunt ut labore et dolore magna aliqua. Ut enim ad minim veniam, quis nostrud</p><span class="btn" style="color:var(--orange)">ADD PHONES</span></div>
<div class="a addon" style="top:908px"><h3>QUIDLOOP</h3><p>Lorem ipsum dolor sit amet, consectetur adipiscing elit, sed do eiusmod tempor incididunt ut labore et dolore magna aliqua. Ut enim ad minim veniam, quis nostrud</p><span class="btn">ACTIVATE</span></div>
<div class="a addon" style="top:985px"><h3>WIRECHAT</h3><p>Lorem ipsum dolor sit amet, consectetur adipiscing elit, sed do eiusmod tempor incididunt ut labore et dolore magna aliqua. Ut enim ad minim veniam, quis nostrud</p><span class="btn">ACTIVATE</span></div>
<div class="a addon" style="top:1062px"><h3>SOCIAL MESSENGER</h3><p>Lorem ipsum dolor sit amet, consectetur adipiscing elit, sed do eiusmod tempor incididunt ut labore et dolore magna aliqua. Ut enim ad minim veniam, quis nostrud</p><span class="btn">ACTIVATE</span></div>
<div class="a mark">M1</div>
</body></html>
```